Kelvaro.ch is looking for business card letterhead and envelope C5 with WOW effect

We need a strong business card for our company Kelvaro.ch, logo is available. You want a black or dark background on which the logo Stark r% 26 # 252; appears. Letterhead and envelope in C5 format should be in a similar design, but does not have to be We need a strong business card for our company Kelvaro.ch, logo is available. A black or dark background is desired, on which the logo Stark comes across. The letterhead and the envelope in C5 format should have a similar design.

Target Market(s)

Private customers as well as entrepreneurs

Contact Information for Business Card

E-mail: info@kelvaro-example.ch
Web.www.Kelvaro-example.ch
Tel: +41 ( 0 ) 79 482 6037
Adresse:
Lindenweg 14
9406 Tarnbach

Hier kann man Icons verwenden für Email,Tel und Adressse

Font styles to use
Other font styles liked:
• Dubai,bold

Colors

Designer to choose colors to be used in the design.

Requirements
Must have
• WOW effect
Nice to have
• R% 26 # 252; back business card with our service listings. - VEHICLE LABELING - SHOP WINDOW LABELING - STICKERS AND MUCH MORE ... in red color

```html
<!DOCTYPE html>
<html lang="en">
<head>
<meta charset="utf-8">
<title>Kelvaro.ch – Business Card</title>
<link href="https://fonts.googleapis.com/css2?family=Lato:wght@400;700;900&display=swap" rel="stylesheet">
<style>
  :root {
    --page-bg: #dedede;
    --card-white: #ffffff;
    --card-black: #070707;
    --brand-yellow: #fdcb1f;
    --brand-yellow-soft: #fde27a;
    --ink-black: #111111;
    --ink-grey: #8a8a8a;
    --ink-white: #ffffff;
    --card-shadow: rgba(0, 0, 0, 0.55);
  }
  * { margin: 0; padding: 0; box-sizing: border-box; }
  html, body {
    width: 1200px;
    height: 960px;
    overflow: hidden;
    background: var(--page-bg);
    font-family: 'Lato', Arial, sans-serif;
  }
  .stage {
    position: relative;
    width: 1200px;
    height: 960px;
  }
  .card {
    position: absolute;
    left: 280px;
    width: 656px;
    height: 374px;
    border-radius: 28px;
    overflow: hidden;
    box-shadow: 0 4px 2px -1px var(--card-shadow);
  }
  .card-front { top: 80px; background: var(--card-white); }
  .card-back { top: 506px; background: var(--card-black); }

  .pattern-area {
    position: absolute;
    top: 0;
    right: 0;
    width: 216px;
    height: 100%;
    background: linear-gradient(160deg, var(--brand-yellow) 0%, var(--brand-yellow-soft) 55%, var(--brand-yellow) 100%);
  }

  .company-name {
    font-weight: 900;
    letter-spacing: 0.5px;
    line-height: 1;
    white-space: nowrap;
  }
  .card-front .company-name {
    position: absolute;
    left: 74px;
    top: 59px;
    font-size: 30px;
    line-height: 30px;
    color: var(--ink-black);
  }

  .person-name {
    position: absolute;
    left: 74px;
    top: 119px;
    font-size: 26px;
    line-height: 28px;
    font-weight: 700;
    color: var(--brand-yellow);
  }
  .person-role {
    position: absolute;
    left: 74px;
    top: 151px;
    font-size: 17.5px;
    line-height: 22px;
    color: var(--ink-grey);
  }
  .address {
    position: absolute;
    left: 74px;
    top: 192px;
    font-size: 17.5px;
    color: var(--ink-grey);
    line-height: 23px;
    font-style: normal;
  }
  .contact-list {
    position: absolute;
    left: 74px;
    top: 249px;
    list-style: none;
    font-size: 17.5px;
    line-height: 24.5px;
    color: var(--ink-grey);
  }
  .contact-item {
    display: flex;
    align-items: center;
    height: 24.5px;
    white-space: nowrap;
  }
  .contact-icon {
    width: 14px;
    height: 14px;
    margin-right: 8px;
    flex: none;
  }

  .back-brand {
    position: absolute;
    left: 177px;
    top: 142px;
    display: flex;
    align-items: center;
  }
  .brand-square {
    width: 64px;
    height: 64px;
    background: var(--brand-yellow);
    margin-right: 36px;
  }
  .card-back .company-name {
    font-size: 34px;
    color: var(--ink-white);
  }
</style>
</head>
<body>
<main class="stage">

  <section class="card card-front" aria-label="Business card front">
    <div class="company-name">Kelvaro.ch</div>
    <h1 class="person-name">Lukas Brenner</h1>
    <p class="person-role">Managing Director</p>
    <address class="address">Lindenweg 14<br>9406 Tarnbach</address>
    <ul class="contact-list">
      <li class="contact-item">
        <svg class="contact-icon" viewBox="0 0 14 14" aria-hidden="true">
          <path d="M3 12 C1 9 2 4 6 2 L8 4 L6 6 C5 7 5 9 6 10 L4 12 Z" fill="var(--brand-yellow)"/>
        </svg>
        +41 ( 0 ) 79 482 6037
      </li>
      <li class="contact-item">
        <svg class="contact-icon" viewBox="0 0 14 14" aria-hidden="true">
          <rect x="1" y="4" width="12" height="7" fill="var(--brand-yellow)"/>
          <path d="M1 4 L7 8.5 L13 4" stroke="var(--card-white)" stroke-width="1.2" fill="none"/>
        </svg>
        info@kelvaro-example.ch
      </li>
      <li class="contact-item">
        <svg class="contact-icon" viewBox="0 0 14 14" aria-hidden="true">
          <g fill="none" stroke="var(--brand-yellow)" stroke-width="1.2">
            <circle cx="7" cy="7" r="5.5"/>
            <ellipse cx="7" cy="7" rx="2.4" ry="5.5"/>
            <line x1="1.5" y1="7" x2="12.5" y2="7"/>
          </g>
        </svg>
        www.kelvaro-example.ch
      </li>
    </ul>
    <div class="pattern-area" role="img" aria-label="Yellow honeycomb pattern of solid and outlined hexagons along the right edge"></div>
  </section>

  <section class="card card-back" aria-label="Business card back">
    <div class="back-brand">
      <div class="brand-square"></div>
      <div class="company-name">Kelvaro.ch</div>
    </div>
  </section>

</main>
</body>
</html>
```